Health Clinic treating people with mental illness needs a website

We need a website for a new mental health clinic based in Florida called Solvane Wellness USA. We treat people with mental health issues such as depression, PTSD, Bipolar, chronic pain, etc. I want the website to be easy to follow and inviting to the visitors. It should be easy to locate the different treatment options and how to go about contacting and making appointments. The images on the website should be something that the patients can relate to, whether a close up of a woman's face, something that conveys emotion. The patients visiting this website are often sad and miserable, they need to be able to feel comfortable when they look at this website. I want them to feel that we understand where they are coming from. I like colors such as purple, turquoise, lavender.

Target Market(s)

College students, veterans, anyone with mental illness

Industry/Entity Type

Health And Wellness

Font styles to use
Serif
Sans Serif

Colors

Designer to choose colors to be used in the design.

Requirements
Must have
• There should be a home/landing page, about us page, treatment page, contact page, and a FAQ page. I've included my logo below.
Nice to have
• The flow of the web pages should be calming and welcoming. I want people to feel warm and understood when they enter our page.
Should not have
• The images and writing should not be overly stimulating or aggressive.

```html
<!DOCTYPE html>
<html lang="en">
<head>
<meta charset="utf-8">
<title>Solvane Wellness USA</title>
<link href="https://fonts.googleapis.com/css2?family=Rubik:wght@500;700&family=Open+Sans:wght@400;600&display=swap" rel="stylesheet">
<style>
:root{
  --purple:#7c1f80;
  --purple-deep:#5a1670;
  --teal:#2aa88f;
  --ink:#2b2b2b;
  --muted:#4a4a4a;
  --blush:#f4f0f1;
  --white:#ffffff;
  --navy:#1f2a5a;
  --line:#cfcfcf;
  --gold:#f4c36a;
}
*{box-sizing:border-box;margin:0;padding:0}
html,body{width:1200px;height:4158px;overflow:hidden}
body{font-family:"Open Sans",Arial,sans-serif;color:var(--ink);background:var(--white);position:relative}
h1,h2,h3,.btn,.nav a,.brand{font-family:"Rubik",Arial,sans-serif}
section,header,footer{position:absolute;left:0;width:1200px}
.abs{position:absolute}

/* header */
.site-header{top:0;height:107px;background:var(--white)}
.brand{left:130px;top:38px;display:flex;align-items:center;gap:10px;font-weight:500;font-size:26px;color:var(--purple)}
.brand-dot{width:18px;height:18px;border-radius:50%;background:var(--purple)}
.nav{left:476px;top:46px;display:flex;gap:34px}
.nav a{font-size:14px;font-weight:500;color:var(--ink);text-decoration:none;letter-spacing:.3px}
.nav a.active{color:var(--purple);text-decoration:underline}
.social{left:973px;top:42px;display:flex;gap:8px}
.social span{width:26px;height:26px;border-radius:50%;background:var(--navy)}
.social span:nth-child(2){background:#1da1f2}
.social span:nth-child(1){background:#3b5998}

/* hero */
.hero{top:107px;height:523px}
.hero-photo{position:absolute;inset:0;background:linear-gradient(180deg,#c9b8a0 0%,#d8b98a 45%,#c89a4a 75%,#a8782f 100%)}
.hero-title{left:778px;top:120px;color:var(--purple);font-weight:700;line-height:1.02}
.hero-title .small{font-size:46px;display:block}
.hero-title .big{font-size:62px;display:block}
.btn{display:inline-flex;align-items:center;justify-content:center;background:var(--teal);color:var(--white);font-weight:500;letter-spacing:.5px;text-decoration:none}
.hero .btn{position:absolute;left:786px;top:331px;width:272px;height:61px;font-size:19px}

/* about */
.about{top:630px;height:455px;background:var(--blush)}
.about-mark{left:135px;top:55px;width:380px;height:350px;display:flex;flex-direction:column;align-items:center;justify-content:center;gap:18px}
.about-mark .ring{width:260px;height:260px;border-radius:50%;border:10px solid var(--gold);opacity:.7}
.about-mark .name{font-family:"Rubik",Arial,sans-serif;font-weight:500;font-size:26px;color:var(--purple)}
.about h2{left:573px;top:70px;font-size:37px;font-weight:700;color:var(--ink)}
.about .copy{left:577px;top:140px;width:500px;font-size:14.5px;line-height:22.5px;color:var(--muted)}
.about .copy p+p{margin-top:29px}

/* why */
.why{top:1085px;height:130px;text-align:center}
.why h2{margin-top:38px;font-size:25px;font-weight:700}
.why p{margin-top:8px;font-size:15px;color:var(--muted)}
.benefits{top:1215px;height:470px;background:linear-gradient(180deg,#2d2a2a,#3e3630 60%,#222)}
.benefit{position:absolute;top:64px;width:297px;height:347px;background:var(--white);text-align:center}
.benefit .ph{height:207px}
.benefit h3{margin-top:29px;font-size:13px;font-weight:500;letter-spacing:.3px}
.benefit p{margin:9px 30px 0;font-size:12.5px;line-height:17px;color:var(--muted)}

/* treatment */
.treatment{top:1685px;height:931px;background:var(--blush)}
.section-title{position:absolute;left:0;width:1200px;text-align:center;font-size:25px;font-weight:700;color:var(--ink)}
.treat-card{position:absolute;width:299px;height:317px;background:var(--white);box-shadow:0 1px 4px rgba(0,0,0,.08)}
.treat-card .ph{height:246px}
.treat-card h3{padding:22px 0 0 26px;font-size:16.5px;font-weight:500;letter-spacing:.3px}
.treatment .btn{position:absolute;left:488px;top:830px;width:224px;height:48px;font-size:14px}

/* faq */
.faq{top:2616px;height:482px;background:var(--white)}
.faq-item{position:absolute;left:292px;width:601px;height:44px;border:1px solid var(--line);display:flex;align-items:center;padding-left:24px;font-size:14.5px;color:var(--ink)}
.faq-item .toggle{position:absolute;right:10px;top:8px;width:34px;height:28px;background:var(--teal);color:var(--white);display:flex;align-items:center;justify-content:center;font-size:18px;font-weight:600}
.faq-item.open .toggle{background:#a04ca6}
.faq-answer{position:absolute;left:292px;top:194px;width:580px;font-size:12.5px;line-height:17px;color:var(--muted)}

/* articles */
.articles{top:3098px;height:549px;background:var(--blush)}
.article{position:absolute;top:119px;width:299px;height:370px;background:var(--white);box-shadow:0 1px 4px rgba(0,0,0,.08)}
.article .ph{height:246px}
.article h3{margin:26px 0 0 26px;font-size:16.5px;font-weight:500;letter-spacing:.3px}
.article p{margin:12px 26px 0;font-size:13.5px;line-height:19px;color:var(--muted)}

/* contact */
.contact{top:3647px;height:442px;background:var(--white)}
.contact-photo{position:absolute;left:0;top:0;width:600px;height:442px;background:linear-gradient(135deg,#8a2a92,#a3479f 55%,#7d2383)}
.contact-info{left:145px;top:100px;color:var(--white)}
.contact-info h2{font-size:28px;font-weight:500;letter-spacing:.5px}
.contact-info p{font-size:12.5px;line-height:23px;margin-top:12px;opacity:.95}
.field{position:absolute;font-size:13px;color:var(--ink);border-bottom:1px solid var(--line);padding-bottom:10px}
.submit{position:absolute;left:656px;top:276px;width:394px;height:42px;background:var(--purple);color:var(--white);font-family:"Rubik",Arial,sans-serif;font-weight:500;font-size:17px;display:flex;align-items:center;justify-content:center;letter-spacing:.5px}

.site-footer{top:4089px;height:69px;background:var(--blush);text-align:center;font-size:12px;line-height:69px;color:var(--ink)}
</style>
</head>
<body>

<header class="site-header">
  <div class="brand abs"><span>Solvane Wellness USA</span><span class="brand-dot"></span></div>
  <nav class="nav abs">
    <a class="active" href="#">HOME</a><a href="#">ABOUT US</a><a href="#">TREATMENT</a><a href="#">FAQ</a><a href="#">CONTACT US</a>
  </nav>
  <div class="social abs" aria-label="Social links"><span></span><span></span><span></span></div>
</header>

<section class="hero">
  <div class="hero-photo" role="img" aria-label="Smiling woman with open arms in a golden wheat field at sunset"></div>
  <h1 class="hero-title abs"><span class="small">WELCOME TO</span><span class="big">SOLVANE</span><span class="big">WELLNESS</span></h1>
  <a class="btn" href="#">BOOK AN APPOINTMENT</a>
</section>

<section class="about">
  <div class="about-mark abs"><div class="ring"></div><div class="name">Solvane Wellness USA</div></div>
  <h2 class="abs">ABOUT US</h2>
  <div class="copy abs">
    <p>Lorem ipsum dolor sit amet, consectetur adipiscing elit, sed do eiusmod tempor incididunt ut labore et dolore magna aliqua. Ut enim ad minim veniam, quis nostrud exercitation ullamco laboris nisi ut aliquip ex ea commodo consequat. Duis aute irure dolor in reprehenderit in voluptate.</p>
    <p>Duis aute irure dolor in reprehenderit in voluptate velit esse cillum dolore eu fugiat nulla pariatur &nbsp;error sit voluptatem accusantium doloremque laudantium, totam rem aperiam, eaque ipsa quae ab illo inventore veritatis</p>
  </div>
</section>

<section class="why">
  <h2>WHY CHOOSE US</h2>
  <p>Lorem ipsum dolor</p>
</section>

<section class="benefits" role="region" aria-label="Why choose us">
  <div class="benefit" style="left:129px">
    <div class="ph" role="img" aria-label="Person raising arms in a meadow at sunset" style="background:linear-gradient(180deg,#8c7a8a,#c9a070 60%,#6b5a3a)"></div>
    <h3>SATISFACTION</h3>
    <p>Duis aute irure dolor in repreh enderit in voluptate velit esse cillum dolore eu fugiat nulla pariatur.</p>
  </div>
  <div class="benefit" style="left:452px">
    <div class="ph" role="img" aria-label="Silhouette leaping toward birds in a golden sky" style="background:linear-gradient(180deg,#e8c990,#d9a050 65%,#3a2a1a)"></div>
    <h3>BETTER HEALTH</h3>
    <p>Duis aute irure dolor in repreh enderit in voluptate velit esse cillum dolore eu fugiat nulla pariatur.</p>
  </div>
  <div class="benefit" style="left:774px">
    <div class="ph" role="img" aria-label="Woman jumping joyfully on a turquoise beach" style="background:linear-gradient(180deg,#d6e6ea,#7fcfcf 55%,#e6dccb)"></div>
    <h3>LOREM IPSUM</h3>
    <p>Duis aute irure dolor in repreh enderit in voluptate velit esse cillum dolore eu fugiat nulla pariatur.</p>
  </div>
</section>

<section class="treatment">
  <h2 class="section-title" style="top:55px">OUR TREATMENT</h2>
  <div class="treat-card" style="left:137px;top:133px"><div class="ph" role="img" aria-label="Woman sitting alone on a sofa looking sad" style="background:linear-gradient(135deg,#5a4538,#8a6a55)"></div><h3>DEPRESSION</h3></div>
  <div class="treat-card" style="left:451px;top:133px"><div class="ph" role="img" aria-label="Distressed woman holding her head" style="background:linear-gradient(135deg,#2a2a2a,#6a6a6a)"></div><h3>PTSD</h3></div>
  <div class="treat-card" style="left:764px;top:133px"><div class="ph" role="img" aria-label="Man sitting on the floor against a wall" style="background:linear-gradient(180deg,#b9c4cc,#8d99a3 70%,#6a4e3a)"></div><h3>BIPOLAR</h3></div>
  <div class="treat-card" style="left:137px;top:471px"><div class="ph" role="img" aria-label="Person holding a painful elbow" style="background:linear-gradient(135deg,#3d4446,#8a9296)"></div><h3>CHRONIC PAIN</h3></div>
  <div class="treat-card" style="left:451px;top:471px"><div class="ph" role="img" aria-label="Woman with open arms against an orange sunset" style="background:linear-gradient(180deg,#f0b84a,#d88a2a 70%,#8a3a1a)"></div><h3>MINDFULNESS</h3></div>
  <div class="treat-card" style="left:764px;top:471px"><div class="ph" role="img" aria-label="Anxious woman sitting on the floor" style="background:linear-gradient(135deg,#c9c9c9,#8e8e92)"></div><h3>ANXIETY</h3></div>
  <a class="btn" href="#">BOOK AN APPOINTMENT</a>
</section>

<section class="faq">
  <h2 class="section-title" style="top:50px">FREQUENTLY ASKED QUESTIONS</h2>
  <div class="faq-item open" style="top:131px">Lorem ipsum dolor sit amet consectetur adipiscing elit?<span class="toggle">&minus;</span></div>
  <p class="faq-answer">Sed ut perspiciatis unde omnis iste natus error sit voluptatem accusantdoloremque laudantium, totam rem aper eaque ipsa quae ab illo inventore veritatis easi architecto beatae vitae dicta sunt explicabo ipsam voluptatem.</p>
  <div class="faq-item" style="top:270px">Lorem ipsum dolor sit amet consectetur adipiscing elit?<span class="toggle">+</span></div>
  <div class="faq-item" style="top:327px">Lorem ipsum dolor sit amet consectetur adipiscing elit?<span class="toggle">+</span></div>
  <div class="faq-item" style="top:384px">Lorem ipsum dolor sit amet consectetur adipiscing elit?<span class="toggle">+</span></div>
</section>

<section class="articles">
  <h2 class="section-title" style="top:48px">LATEST ARTICLES</h2>
  <div class="article" style="left:131px"><div class="ph" role="img" aria-label="Woman tossing autumn leaves in a park" style="background:linear-gradient(180deg,#e6a23a,#d1502a 60%,#a0302a)"></div><h3>LOREM IPSUM IS SIMPLY</h3><p>Sed ut perspiciatis unde omnis iste natus error sit voluptatem.</p></div>
  <div class="article" style="left:451px"><div class="ph" role="img" aria-label="Woman in a hat among daisies under a blue sky" style="background:linear-gradient(180deg,#3f7fc6,#8fbbe0 55%,#5f8a45)"></div><h3>LOREM IPSUM IS SIMPLY</h3><p>Sed ut perspiciatis unde omnis iste natus error sit voluptatem.</p></div>
  <div class="article" style="left:770px"><div class="ph" role="img" aria-label="Smiling woman by the sea with windswept hair" style="background:linear-gradient(135deg,#d9e3ea,#8fb0c8 60%,#b08a6a)"></div><h3>LOREM IPSUM IS SIMPLY</h3><p>Sed ut perspiciatis unde omnis iste natus error sit voluptatem.</p></div>
</section>

<section class="contact">
  <div class="contact-photo" role="img" aria-label="Two women talking, tinted purple"></div>
  <div class="contact-info abs">
    <h2>GET IN TOUCH</h2>
    <p>I'm a paragraph. Click here to add your<br>own text and edit me.</p>
    <p>Address: 214 Harbor Palm Avenue<br>Tampa, FL 33602</p>
    <p>Email: info@solvanewellness.com<br>Phone: 813-555-0147</p>
  </div>
  <div class="field" style="left:656px;top:98px;width:178px">First Name</div>
  <div class="field" style="left:872px;top:98px;width:178px">Last Name</div>
  <div class="field" style="left:656px;top:155px;width:178px">Email</div>
  <div class="field" style="left:872px;top:155px;width:178px">Subject</div>
  <div class="field" style="left:656px;top:211px;width:394px">Type your message here...</div>
  <div class="submit">SUBMIT</div>
</section>

<footer class="site-footer">Copyright © 2019 All Rights Reserved</footer>

</body>
</html>
```